The Linen Loft Co

We need a business card design for our wardrobe company.
Please visit our website www.gentlelinenlofts.com to get an idea of who we are.

```html
<!DOCTYPE html>
<html lang="en">
<head>
<meta charset="UTF-8">
<title>The Linen Loft Co — Business Card</title>
<link href="https://fonts.googleapis.com/css2?family=Poppins:wght@400;500;600&display=swap" rel="stylesheet">
<style>
  :root {
    --page-bg: #e9e6e2;
    --card-bg: #ffffff;
    --ink: #111111;
    --muted: #555555;
    --soft: #a8a8a8;
    --frame: #1a1a1a;
  }
  * { margin: 0; padding: 0; box-sizing: border-box; }
  html, body {
    width: 1200px;
    height: 989px;
    overflow: hidden;
    background: var(--page-bg);
    font-family: "Poppins", sans-serif;
  }
  .business-card {
    position: absolute;
    left: 80px;
    top: 195px;
    width: 1040px;
    height: 598px;
    background: var(--card-bg);
    box-shadow: 0 4px 14px rgba(0,0,0,0.12);
  }
  .card-frame {
    position: absolute;
    inset: 22px 24px 24px 22px;
    border: 2px solid var(--frame);
  }
  .brand {
    position: absolute;
    left: 86px;
    top: 263px;
    display: flex;
    align-items: center;
    gap: 26px;
  }
  .brand-mark {
    width: 68px;
    height: 68px;
    border: 3px solid var(--ink);
    flex: none;
  }
  .brand-name {
    font-size: 21px;
    font-weight: 600;
    color: var(--ink);
    letter-spacing: -0.2px;
    text-transform: uppercase;
    line-height: 1.2;
  }
  .contact {
    position: absolute;
    left: 547px;
    top: 160px;
    color: var(--muted);
  }
  .contact-name {
    font-size: 40px;
    font-weight: 600;
    color: var(--ink);
    line-height: 1.1;
  }
  .contact-role {
    font-size: 26px;
    font-weight: 500;
    color: var(--soft);
    line-height: 1.2;
    margin-bottom: 16px;
  }
  .contact-address,
  .contact-lines {
    font-size: 25px;
    font-weight: 400;
    line-height: 1.3;
  }
  .contact-address { margin-bottom: 16px; }
</style>
</head>
<body>
  <div class="business-card">
    <div class="card-frame"></div>

    <div class="brand">
      <div class="brand-mark"></div>
      <p class="brand-name">The Linen Loft Co</p>
    </div>

    <div class="contact">
      <p class="contact-name">Daniel Hartley</p>
      <p class="contact-role">President</p>
      <p class="contact-address">Marlow Court, 42 Fenwick Lane,<br>London N1 4QS</p>
      <p class="contact-lines">Ph. 020 7946 0321<br>info@gentlelinenlofts.com<br>www.gentlelinenlofts.com</p>
    </div>
  </div>
</body>
</html>
```